SnackOrbit!!! A Vending Machine Business Looking for an attractive website.

We are a vending machine business in Northern Michigan. We have changed our name and have rebranded our company. We would like an attractive website that shares who we are, what services we provide, the products we offer in our machines, along with a form businesses can fill out to see if they are a good fit for our company. I would like to have a Home Page, About SnackOrbit, Why Choose SnackOrbit?, Products & Services, Contact Us (With a Login Option), and a page with a questionnaire for thos interested in getting a FREE Vending Machine.

Target Market(s)

Businesses, Campgrounds, Schools, and many more in Northern Michigan

Industry/Entity Type

Vending Machines

Coding

Coded - Design and coding required

Number of Pages Required

5+ page

Requirements
Must have
• An inviting and enticing Home Page. I want to get my potential clients engaged in our website.
Nice to have
• Possibly background photos from Northern Michigan
Should not have
• A corporate feel. I do not want a boring website.

```html
<!DOCTYPE html>
<html lang="en">
<head>
<meta charset="UTF-8">
<title>SnackOrbit – Vending in Northern Michigan</title>
<link href="https://fonts.googleapis.com/css2?family=Dela+Gothic+One&family=Josefin+Sans:wght@400;600;700&display=swap" rel="stylesheet">
<style>
:root{
  --navy:#1c1c5e;
  --green:#2e5a27;
  --green-dark:#244a1f;
  --text:#3a3a3a;
  --light:#f4f4f4;
  --white:#ffffff;
}
*{box-sizing:border-box;margin:0;padding:0}
html,body{width:1200px;height:4360px;overflow:hidden}
body{font-family:"Josefin Sans",sans-serif;color:var(--text);background:var(--white);position:relative}
.display{font-family:"Dela Gothic One",sans-serif;font-weight:400}
section,header,footer{position:relative;width:1200px}
.abs{position:absolute}
.btn{display:inline-block;background:var(--green);color:var(--white);font-family:"Dela Gothic One",sans-serif;font-size:14px;border-radius:22px;padding:12px 22px;text-decoration:none;letter-spacing:.2px}

/* nav */
.site-nav{height:80px;background:var(--white)}
.brand{left:110px;top:27px;font-size:19px;line-height:26px;color:var(--navy);display:flex;align-items:center;gap:8px;white-space:nowrap}
.brand-dot{width:12px;height:12px;background:var(--navy)}
.menu{left:298px;top:0;height:80px;display:flex;gap:26px;align-items:center;font-size:15px;color:var(--navy)}
.menu a{color:var(--navy);text-decoration:none;height:80px;display:flex;align-items:center;position:relative}
.menu a.active{color:var(--green)}
.menu a.active::before{content:"";position:absolute;top:0;left:0;right:0;height:4px;background:var(--navy)}
.login{right:111px;top:22px;padding:11px 38px}

/* hero */
.hero{height:592px}
.hero-bg{inset:0;background:linear-gradient(180deg,#f1f1f1,#e4e4e4)}
.hero-machines{left:90px;top:80px;width:560px;height:510px;background:linear-gradient(120deg,#c81d1d 0%,#e23030 45%,#444 100%);border-radius:8px;opacity:.85}
.hero-text{right:111px;top:170px;text-align:right;width:420px}
.hero-text .welcome{font-size:30px;color:var(--green)}
.hero-text .title{font-size:54px;color:var(--navy);line-height:1.2;margin-top:8px;white-space:nowrap}
.hero-text p{font-size:21px;line-height:28px;margin-top:6px;color:#333}
.hero-text .btn{margin-top:12px;font-size:15px}

/* who */
.who{height:540px}
.who-img{left:112px;top:98px;width:447px;height:341px;background:linear-gradient(135deg,#3f6c6c,#8fb1ab)}
.who-text{left:643px;top:106px;width:446px}
.who-text h2{font-size:36px;color:var(--navy)}
.who-text p{font-size:16px;line-height:28.4px;margin-top:18px}
.who-text .btn{margin-top:18px}

/* why */
.why{height:806px;background:var(--light)}
.section-title{width:100%;text-align:center;font-size:36px;color:var(--navy)}
.why .section-title{top:50px}
.why-frame{left:437px;top:144px;width:324px;height:577px;border:2px solid #333;padding:6px;background:var(--white)}
.why-frame div{width:100%;height:100%;background:linear-gradient(160deg,#2c7bbf,#1e5d96)}
.feat{width:300px}
.feat h3{font-family:"Josefin Sans",sans-serif;font-weight:700;font-size:18px;color:var(--navy);margin-top:8px}
.feat p{font-size:16px;line-height:25.6px;margin-top:10px}
.feat .more{display:inline-block;margin-top:10px;font-weight:700;font-size:15px;color:var(--green);text-decoration:underline}
.feat.right{text-align:right}
.icon{width:44px;height:44px}

/* services */
.services{height:792px}
.services .section-title{top:90px}
.tabs{top:174px;left:0;width:100%;display:flex;justify-content:center;gap:10px}
.tab{font-family:"Dela Gothic One",sans-serif;font-size:13px;color:var(--navy);border:1.5px solid #999;border-radius:22px;height:42px;display:flex;align-items:center;justify-content:center;background:var(--white)}
.tab.active{background:var(--green);color:var(--white);border-color:var(--green)}
.svc-text{left:112px;top:280px;width:530px}
.svc-text h3{font-size:24px;color:var(--navy);display:flex;align-items:center;gap:8px}
.svc-text p{font-size:16px;line-height:28.3px;margin-top:28px}
.svc-text .btn{margin-top:24px;font-size:15px}
.svc-img{left:700px;top:232px;width:389px;height:530px;background:linear-gradient(160deg,#e9edf2,#9aa5b1 55%,#2d5aa6)}

/* products */
.products{height:688px;background:var(--light)}
.products .section-title{top:72px}
.card{top:148px;width:316px}
.card .pimg{width:316px;height:310px}
.card h4{font-size:22px;line-height:28px;color:var(--navy);margin-top:20px}
.card .price{font-size:23px;color:var(--navy);margin-top:2px}
.card .btn{margin-top:14px;padding:11px 22px}
.badge{position:absolute;right:10px;width:40px;height:40px;border-radius:50%;background:var(--white);display:flex;align-items:center;justify-content:center;font-size:11px;color:var(--navy);font-weight:700}
.dots{top:642px;left:0;width:100%;display:flex;justify-content:center;gap:10px}
.dots span{width:10px;height:10px;border-radius:50%;background:var(--navy)}
.dots span.on{background:var(--green)}

/* cta */
.cta{margin-top:97px;height:290px;background:var(--green);color:var(--white);text-align:center;padding-top:50px}
.cta h2{font-size:36px;line-height:48px}
.cta p{font-size:20px;line-height:34px;margin-top:14px}

/* footer */
.site-footer{height:475px;background:var(--navy);color:var(--white)}
.foot-brand{left:110px;top:150px;font-size:44px;line-height:60px;color:var(--white);display:flex;align-items:center;gap:12px;white-space:nowrap}
.foot-brand .sq{width:18px;height:18px;background:var(--white)}
.social{left:250px;top:258px;display:flex;gap:18px}
.social span{width:50px;height:50px;border-radius:50%;background:var(--white)}
.foot-col{top:132px}
.foot-col h5{font-family:"Dela Gothic One",sans-serif;font-weight:400;font-size:19px}
.foot-col ul{list-style:none;margin-top:18px}
.foot-col li{font-size:16px;line-height:36px}
.contact-row{display:flex;align-items:center;gap:12px;margin-top:18px;font-size:15px;line-height:20px}
.contact-row .ci{width:42px;height:42px;border-radius:50%;background:var(--green);display:flex;align-items:center;justify-content:center;flex:none}
.copyright{top:408px;width:100%;text-align:center;font-size:18px}
</style>
</head>
<body>

<header class="site-nav">
  <div class="abs brand display"><span class="brand-dot"></span>SnackOrbit</div>
  <nav class="abs menu">
    <a href="#" class="active">Home</a>
    <a href="#">About SnackOrbit</a>
    <a href="#">Why Choose SnackOrbit?</a>
    <a href="#">Products &amp; Services</a>
    <a href="#">Contact Us</a>
  </nav>
  <a href="#" class="abs btn login">LOGIN</a>
</header>

<section class="hero">
  <div class="abs hero-bg" role="img" aria-label="White painted brick wall background"></div>
  <div class="abs hero-machines" role="img" aria-label="Two red vending machines, one with drink cans and one with snack buttons"></div>
  <div class="abs hero-text">
    <div class="welcome display">Welcome To</div>
    <div class="title display">SnackOrbit</div>
    <p>Lorem ipsum dolor sit amet, onsectetur<br>.adipiscing elit, sed do</p>
    <a href="#" class="btn">GET A QUESTIONNAIRE</a>
  </div>
</section>

<section class="who">
  <div class="abs who-img" role="img" aria-label="White snack and drink vending machine against a teal backdrop"></div>
  <div class="abs who-text">
    <h2 class="display">Who We Are</h2>
    <p>Welcome to SnackOrbit, where snacking meets delight! We're not just about vending machines; we're your culinary companions, your flavor curators, and your secret stash of happiness. Owen and Clara, the dynamic duo behind SnackOrbit, have a passion for all things tasty. With backgrounds in sales and a penchant for personal connections, they've transformed the vending experience into an art form.</p>
    <a href="#" class="btn">READ MORE</a>
  </div>
</section>

<section class="why">
  <h2 class="abs section-title display">Why Choose SnackOrbit?</h2>

  <div class="abs feat" style="left:110px;top:140px">
    <svg class="icon" viewBox="0 0 44 44"><path d="M22 38 L6 22 A9 9 0 0 1 22 10 A9 9 0 0 1 38 22 Z" fill="var(--green)"/></svg>
    <h3>1. Local Love</h3>
    <p>We celebrate the heart of Michigan by partnering with local legends. Say hello to Birch Hollow Jerky and Pine Shore Crisps—our hometown heroes.</p>
    <a class="more">Read More</a>
  </div>

  <div class="abs feat" style="left:110px;top:450px">
    <svg class="icon" viewBox="0 0 44 44"><circle cx="16" cy="13" r="8" fill="var(--green)"/><path d="M3 42 Q3 24 16 24 Q29 24 29 42 Z" fill="var(--green)"/><rect x="30" y="16" width="12" height="10" rx="3" fill="var(--green)"/></svg>
    <h3>2. Unleash Your Cravings</h3>
    <p>SnackOrbit isn't bound by corporate ties. We're the rebels of the vending world. Craving a bag of crispy, kettle-cooked chips? done.Hankering for jerky that packs a punch?<br>We've got you covered.</p>
    <a class="more">Read More</a>
  </div>

  <div class="abs why-frame"><div role="img" aria-label="Blue snack vending machine stocked with chips and candy"></div></div>

  <div class="abs feat right" style="left:789px;top:130px">
    <svg class="icon" viewBox="0 0 44 44"><circle cx="22" cy="22" r="20" fill="var(--green)"/><path d="M13 22 L20 29 L32 16" stroke="#fff" stroke-width="4" fill="none" stroke-linecap="round"/></svg>
    <h3>3. Quality Meets Convenience</h3>
    <p>Imagine this: You're mid-meeting, and your stomach growls. Fear not! SnackOrbit's machines offer top-notch snacks and beverages. It's like having a mini food festival at your fingertips.</p>
    <a class="more">Read More</a>
  </div>

  <div class="abs feat right" style="left:789px;top:448px">
    <svg class="icon" viewBox="0 0 44 44"><circle cx="20" cy="24" r="17" fill="none" stroke="var(--green)" stroke-width="3"/><circle cx="34" cy="10" r="8" fill="var(--green)"/><line x1="8" y1="36" x2="32" y2="12" stroke="var(--green)" stroke-width="3"/></svg>
    <h3>4. Pandemic-Proof &amp; Recession<br>-Ready</h3>
    <p>Life throws curveballs, but SnackOrbit stands strong. Our vending machines are theunsung heroes of resilience.</p>
    <a class="more">Read More</a>
  </div>
</section>

<section class="services">
  <h2 class="abs section-title display">Our Services</h2>
  <div class="abs tabs">
    <div class="tab active" style="width:182px">FOOD &amp; SNAKS</div>
    <div class="tab" style="width:166px">DRINKS &amp; COFEE</div>
    <div class="tab" style="width:192px">GUMBALL &amp; CANDY</div>
    <div class="tab" style="width:190px">COLD &amp; FROZEN</div>
  </div>
  <div class="abs svc-text">
    <h3 class="display">FOOD &amp; SNAKS
      <svg width="44" height="50" viewBox="0 0 44 50"><rect x="4" y="10" width="16" height="36" rx="2" fill="var(--navy)"/><rect x="18" y="26" width="24" height="8" rx="4" fill="var(--green)"/><rect x="18" y="36" width="24" height="8" rx="3" fill="var(--navy)"/></svg>
    </h3>
    <p>Lorem ipsum dolor sit amet, consectetur adipiscing elit, sed mpor incididunt ut labore et dolore magna aliqua. Quis ipsum spendisse ultrices gravida. Risus commodo viverra maecenas ccumsan lacus vel facilisis.Lorem ipsum dolor sit amet, onsectetur it,sed do usmod tempor incididunt ut et lore magna liqua. Quis spendissehy ultrices gravida. Risus commodo viverra maecenas accumsan lacus vel facilisis. Lorem ipsum dolor sit amet, consectetur adipiscingfgs elit, sed do eiusmod tempor incididunt ut labore et dolore magna aliqua. Quis ipsum suspendisse ultrices gravida. Risus commodosd viverra maecenas accumsan lacus vel facilisis.</p>
    <a href="#" class="btn">LEARN MORE</a>
  </div>
  <div class="abs svc-img" role="img" aria-label="Stainless steel snack vending machine with blue side panel"></div>
</section>

<section class="products">
  <h2 class="abs section-title display">Our Products</h2>

  <div class="abs card" style="left:110px">
    <div class="pimg" role="img" aria-label="White drinks and coffee vending machine" style="background:linear-gradient(160deg,#f2f2f2,#d6d6d6)"></div>
    <h4 class="display">DRINKS &amp; COFEE<br>VENDING MACHINE</h4>
    <div class="price display">$256</div>
    <a href="#" class="btn">BUY NOW</a>
  </div>

  <div class="abs card" style="left:441px">
    <div class="pimg" role="img" aria-label="Turquoise and coral gumball and candy vending machine" style="background:linear-gradient(160deg,#5fd1d6,#2fb6c2)"></div>
    <div class="badge" style="top:12px"><svg width="20" height="18" viewBox="0 0 20 18"><path d="M10 18 L1 9 A5 5 0 0 1 10 3 A5 5 0 0 1 19 9 Z" fill="#d62b2b"/></svg></div>
    <div class="badge" style="top:62px">NEW</div>
    <h4 class="display">GUMBALL &amp; CANDY<br>VENDING MACHINE</h4>
    <div class="price display">$226</div>
    <a href="#" class="btn">BUY NOW</a>
  </div>

  <div class="abs card" style="left:773px">
    <div class="pimg" role="img" aria-label="Silver cold and frozen snack vending machine on lavender backdrop" style="background:linear-gradient(160deg,#e6e6fb,#b9b1a0)"></div>
    <h4 class="display">COLD &amp; FROZEN<br>VENDING MACHINE</h4>
    <div class="price display">$156</div>
    <a href="#" class="btn">BUY NOW</a>
  </div>

  <div class="abs dots"><span></span><span class="on"></span><span></span></div>
</section>

<section class="cta">
  <h2 class="display">READY TO EXPERIENCE THE SNACKORBIT<br>DIFFERENCE?</h2>
  <p>Sign up now and let's connect. Taste the future of snacking firsthand! Contact us todayand<br>explore how our vending magic can elevate your space.</p>
</section>

<footer class="site-footer">
  <div class="abs foot-brand display"><span class="sq"></span>SnackOrbit</div>
  <div class="abs social" aria-label="Social links"><span></span><span></span><span></span></div>

  <div class="abs foot-col" style="left:617px">
    <h5>Quick Links</h5>
    <ul>
      <li>Home</li>
      <li>About SnackOrbit</li>
      <li>Why Choose SnackOrbit?</li>
      <li>Products &amp; Services</li>
      <li>Contact Us</li>
    </ul>
  </div>

  <div class="abs foot-col" style="left:840px;width:250px">
    <h5>Contact Us</h5>
    <div class="contact-row">
      <span class="ci"><svg width="20" height="16" viewBox="0 0 20 16"><rect x="1" y="1" width="18" height="14" rx="2" fill="none" stroke="#fff" stroke-width="2"/><path d="M1 2 L10 9 L19 2" fill="none" stroke="#fff" stroke-width="2"/></svg></span>
      <span>hello@snackorbit.example</span>
    </div>
    <div class="contact-row">
      <span class="ci"><svg width="16" height="22" viewBox="0 0 16 22"><path d="M8 21 C8 21 1 12 1 8 A7 7 0 0 1 15 8 C15 12 8 21 8 21 Z" fill="#fff"/><circle cx="8" cy="8" r="3" fill="var(--green)"/></svg></span>
      <span>Lorem ipsum dolor sit<br>SnackOrbit.USA</span>
    </div>
    <div class="contact-row">
      <span class="ci"><svg width="18" height="18" viewBox="0 0 18 18"><path d="M3 1 L7 1 L8 5 L6 7 Q8 11 11 12 L13 10 L17 11 L17 15 Q17 17 15 17 Q1 16 1 3 Q1 1 3 1 Z" fill="#fff"/></svg></span>
      <span>+1(555)010 4477</span>
    </div>
  </div>

  <div class="abs copyright">Copyright © 2024 SnackOrbit | All Rights Reserved</div>
</footer>

</body>
</html>
```